Business Card for a Creative Technology based HR services company

Our company name is Lumo8, and we build large communities of HR (human resource) and finance personnels through our mobile platform, and we conduct lots of on-line and off-line activities to get everyone constantly connected. Behind all these, we will also provide on-site HR and finance contractors to our clients, plus a host of other HR-related services. No process in our company takes more than 5-steps.
Our company slogan: Touching Your Future
Target Market(s)
All human resource (HR) and finance personnels, from new entrants to highly experienced senior professionals.
Industry/Entity Type
Finance
Colors
Designer to choose colors to be used in the design.
Look and feel
Each slider illustrates characteristics of the customer's brand and the style your logo design should communicate.

```html
<!DOCTYPE html>
<html lang="en">
<head>
<meta charset="utf-8">
<title>Lumo8 Business Card</title>
<link href="https://fonts.googleapis.com/css2?family=Exo+2:ital,wght@0,400;0,600;0,800;1,400&display=swap" rel="stylesheet">
<style>
  :root {
    --navy: #0c2f5e;
    --red: #e3262e;
    --ink: #3b3f46;
    --muted: #6b7078;
    --paper: #ffffff;
    --backdrop: #e9eaec;
  }
  * { box-sizing: border-box; margin: 0; padding: 0; }
  html, body { width: 1200px; height: 901px; overflow: hidden; }
  body {
    background: var(--backdrop);
    font-family: "Exo 2", sans-serif;
    display: flex;
    align-items: center;
    justify-content: center;
    gap: 40px;
  }
  .card {
    position: relative;
    width: 540px;
    height: 310px;
    background: var(--paper);
    border-radius: 22px;
    overflow: hidden;
    box-shadow: 0 6px 18px rgba(0,0,0,0.12);
  }
  .wordmark {
    font-weight: 800;
    color: var(--navy);
    letter-spacing: -0.5px;
    line-height: 1;
    display: flex;
    align-items: center;
    gap: 8px;
  }
  .wordmark .dot {
    width: 14px; height: 14px;
    border-radius: 50%;
    background: var(--red);
  }
  .card-front .wordmark {
    position: absolute;
    top: 34px; right: 38px;
    font-size: 44px;
  }
  .identity {
    position: absolute;
    top: 36px; left: 34px;
  }
  .identity .name {
    color: var(--red);
    font-size: 17px;
    font-weight: 400;
    letter-spacing: 1px;
    text-transform: uppercase;
  }
  .identity .role {
    color: var(--muted);
    font-size: 12px;
    font-style: italic;
    margin-top: 2px;
  }
  .identity .address {
    color: var(--ink);
    font-size: 12px;
    line-height: 1.45;
    margin-top: 12px;
  }
  .contacts {
    position: absolute;
    right: 34px;
    bottom: 66px;
    list-style: none;
    text-align: right;
  }
  .contacts li {
    display: flex;
    align-items: center;
    justify-content: flex-end;
    gap: 8px;
    font-size: 11.5px;
    color: var(--ink);
    line-height: 1.75;
  }
  .contacts svg { width: 11px; height: 11px; fill: var(--red); }
  .accent-band {
    position: absolute;
    left: 0; bottom: 0;
    width: 100%; height: 40px;
    background: var(--navy);
  }
  .card-back {
    display: flex;
    align-items: center;
    justify-content: center;
  }
  .card-back .wordmark { font-size: 64px; }
  .card-back .wordmark .dot { width: 18px; height: 18px; }
</style>
</head>
<body>

  <section class="card card-front">
    <div class="wordmark">Lumo8<span class="dot"></span></div>

    <div class="identity">
      <p class="name">Daniel Mercer</p>
      <p class="role">Managing Director</p>
      <p class="address">27 9th Floor/Plaza<br>Harbour Road TRN</p>
    </div>

    <ul class="contacts">
      <li>020 481 3357
        <svg viewBox="0 0 24 24"><path d="M6.6 10.8a15.1 15.1 0 0 0 6.6 6.6l2.2-2.2c.3-.3.7-.4 1-.2 1.1.4 2.3.6 3.6.6.6 0 1 .4 1 1V20c0 .6-.4 1-1 1A17 17 0 0 1 3 4c0-.6.4-1 1-1h3.5c.6 0 1 .4 1 1 0 1.3.2 2.5.6 3.6.1.3 0 .7-.2 1z"/></svg></li>
      <li>020 481 3358
        <svg viewBox="0 0 24 24"><path d="M7 2h10a2 2 0 0 1 2 2v16a2 2 0 0 1-2 2H7a2 2 0 0 1-2-2V4a2 2 0 0 1 2-2zm0 3v13h10V5z"/></svg></li>
      <li>020 481 3359
        <svg viewBox="0 0 24 24"><path d="M6 2h10v5H6zM4 8h16a2 2 0 0 1 2 2v7h-4v5H6v-5H2v-7a2 2 0 0 1 2-2zm4 8v4h8v-4z"/></svg></li>
      <li>daniel@lumo8mail.com
        <svg viewBox="0 0 24 24"><path d="M2 5h20v14H2zm2 2v.5l8 5 8-5V7l-8 5z"/></svg></li>
      <li>www.lumo8hub.com
        <svg viewBox="0 0 24 24"><path d="M12 2a10 10 0 1 0 0 20 10 10 0 0 0 0-20zm6.9 9h-3a15 15 0 0 0-1.4-6 8 8 0 0 1 4.4 6zM12 4c.9 1.3 1.7 3.8 1.9 7h-3.8c.2-3.2 1-5.7 1.9-7zM9.5 5a15 15 0 0 0-1.4 6h-3a8 8 0 0 1 4.4-6zm-4.4 8h3a15 15 0 0 0 1.4 6 8 8 0 0 1-4.4-6zM12 20c-.9-1.3-1.7-3.8-1.9-7h3.8c-.2 3.2-1 5.7-1.9 7zm2.5-1a15 15 0 0 0 1.4-6h3a8 8 0 0 1-4.4 6z"/></svg></li>
    </ul>

    <div class="accent-band" role="img" aria-label="Navy decorative wave accent along the card edge"></div>
  </section>

  <section class="card card-back">
    <div class="wordmark">Lumo8<span class="dot"></span></div>
  </section>

</body>
</html>
```